Stationery for Villa Marenta Design Hotel**

Who we are:

Wander on an isolated beach while breathing in the fresh, salty, sea air. Listen to the warm Pacific wind rustling through green palm trees as you walk to a pristine lagoon. Feel the delicious warmth of the sun kiss your skin; the beach is yours. At Villa Marenta you can experience a vacation in undisturbed, natural beauty. We have created a place for you to find new strength, relaxation, and inner harmony. We offer total rest to the experienced traveler from all over the world.

We are a brand new and smartly built design-hotel (under construction) close to a unique beach and a fantastic surf spot in Huatulco, Southwest Mexico.

As you can see in the attachments, we do have an established corporate design, but as for now still need a format for booklets for information around our hotel and things to do in the area, important numbers (we fill in the content for that one).

Our corporate colors:
green #64b445, brown #b07043, blue #0ab7cf, yellow # f9b02a and #fcc01a, navy #444f69
Corporate fonts:
Krub and Miller Banner.
For further information access:
www.villamarenta.example
https://slidevault.example/view/QmPxLwZrTyKsNbVcHdJe/

Social Media: VillaMarenta

Industry/Entity Type

Hotel

Font styles to use
Other font styles liked:
• Krub, Miller Banner

Requirements
Must have
• Stick to Logo Design, defined corporate elements, logo, colors, fonts and general touch and feel
Nice to have
• Who we are:

Our corporate colors:
Corporate fonts:
Krub and Miller Banner.
www.villamarenta.example

Social Media: VillaMarenta

```html
<!DOCTYPE html>
<html lang="en">
<head>
<meta charset="utf-8">
<title>Villa Marenta Design Hotel — Letterhead</title>
<link rel="stylesheet" href="https://fonts.googleapis.com/css2?family=Krub:wght@500&family=Libre+Baskerville&display=swap">
<style>
  :root {
    --backdrop: #dfe3e5;
    --paper: #ffffff;
    --gold: #d9a21f;
    --accent-start: #0ab7cf;
    --accent-end: #64b445;
    --teal-text: #1d8f97;
    --grey-text: #7a7a7a;
    --rule: #9a9a9a;
  }
  * { box-sizing: border-box; margin: 0; padding: 0; }
  html, body { width: 1200px; height: 784px; overflow: hidden; }
  body {
    background: var(--backdrop);
    display: flex;
    align-items: center;
    justify-content: center;
  }
  .letterhead {
    position: relative;
    width: 524px;
    height: 740px;
    background: var(--paper);
    box-shadow: 0 6px 18px rgba(0,0,0,0.12);
    overflow: hidden;
  }
  .accent-area {
    position: absolute;
    width: 110px;
    height: 80px;
    background: linear-gradient(135deg, var(--accent-start), var(--accent-end));
  }
  .accent-area--top {
    top: 0; left: 0;
    clip-path: polygon(0 0, 100% 0, 0 100%);
  }
  .accent-area--bottom {
    bottom: 0; right: 0;
    clip-path: polygon(100% 0, 100% 100%, 0 100%);
  }

  .brand {
    position: absolute;
    top: 70px;
    left: 0; right: 0;
    display: flex;
    align-items: center;
    justify-content: center;
    gap: 10px;
  }
  .brand__mark {
    width: 14px; height: 14px;
    border: 2px solid var(--gold);
  }
  .brand__name {
    font-family: "Krub", sans-serif;
    font-weight: 500;
    font-size: 24px;
    letter-spacing: 2px;
    text-transform: uppercase;
    color: var(--gold);
  }

  .footer {
    position: absolute;
    bottom: 90px;
    left: 0; right: 0;
    text-align: center;
  }
  .footer__icons {
    display: flex;
    align-items: center;
    justify-content: center;
    gap: 7px;
    margin-bottom: 8px;
  }
  .footer__rule { width: 60px; height: 1px; background: var(--rule); margin: 0 10px; }
  .footer__icons svg { width: 13px; height: 13px; }
  .footer__address {
    font-family: "Libre Baskerville", serif;
    font-size: 10.5px;
    color: var(--teal-text);
    margin-bottom: 4px;
  }
  .footer__contact {
    font-family: "Libre Baskerville", serif;
    font-size: 9.5px;
    color: var(--grey-text);
  }
</style>
</head>
<body>
  <main class="letterhead">
    <div class="accent-area accent-area--top" role="img" aria-label="Corner accent graphic in the hotel colours"></div>

    <div class="brand">
      <span class="brand__mark"></span>
      <span class="brand__name">Villa Marenta</span>
    </div>

    <footer class="footer">
      <div class="footer__icons">
        <span class="footer__rule"></span>
        <svg viewBox="0 0 14 14" aria-label="Location"><circle cx="7" cy="7" r="7" fill="var(--gold)"/><path d="M7 3.2a2.3 2.3 0 0 1 2.3 2.3C9.3 7.3 7 10.5 7 10.5S4.7 7.3 4.7 5.5A2.3 2.3 0 0 1 7 3.2z" fill="#fff"/></svg>
        <svg viewBox="0 0 14 14" aria-label="Phone"><circle cx="7" cy="7" r="7" fill="var(--gold)"/><path d="M4.5 3.5l1.5 1.5-.8 1c.5 1 1.3 1.8 2.3 2.3l1-.8 1.5 1.5-1 1c-2.5-.5-4.5-2.5-5-5z" fill="#fff"/></svg>
        <svg viewBox="0 0 14 14" aria-label="Clock"><circle cx="7" cy="7" r="7" fill="var(--gold)"/><circle cx="7" cy="7" r="3.2" fill="none" stroke="#fff" stroke-width="1"/></svg>
        <svg viewBox="0 0 14 14" aria-label="Email"><circle cx="7" cy="7" r="7" fill="var(--gold)"/><rect x="3.6" y="4.6" width="6.8" height="4.8" fill="none" stroke="#fff" stroke-width="1"/><path d="M3.6 4.6L7 7.3l3.4-2.7" fill="none" stroke="#fff" stroke-width="1"/></svg>
        <svg viewBox="0 0 14 14" aria-label="Website"><circle cx="7" cy="7" r="7" fill="var(--gold)"/><circle cx="7" cy="7" r="3.4" fill="none" stroke="#fff" stroke-width="0.9"/><path d="M3.6 7h6.8M7 3.6v6.8" stroke="#fff" stroke-width="0.9"/></svg>
        <span class="footer__rule"></span>
      </div>
      <p class="footer__address">Villa Marenta, Punta Salina, Costa Verde, Mexiko</p>
      <p class="footer__contact">+52 | (000) 555 0142 | hello@villamarenta.example | www.villamarenta.example</p>
    </footer>

    <div class="accent-area accent-area--bottom" role="img" aria-label="Corner accent graphic in the hotel colours"></div>
  </main>
</body>
</html>
```